BUSINESS CARD DESIGN

NAME- DALE VORSKIN
PHONE NUMER - 555- 714-9082
EMAIL- OFFICE@TRV-GROUNDMAKRZ.COM
BACK OF CARD- SPEACIALIZES IN LAND CLEARING, FORESTRY MUCLHING AND EXCAVATION

Contact Information for Business Card

NAME- DALE VORSKIN PHONE NUMER - 555- 714-9082 EMAIL- OFFICE@TRV-GROUNDMAKRZ.COM BACK OF CARD- SPEACIALIZES IN LAND CLEARING , MUCLHING AND EXCAVATION

```html
<!DOCTYPE html>
<html lang="en">
<head>
<meta charset="utf-8">
<title>Traverse Groundmakrz – Business Card</title>
<link href="https://fonts.googleapis.com/css2?family=Roboto:wght@300;400;500;700&display=swap" rel="stylesheet">
<style>
  :root {
    --backdrop: #e3e7e8;
    --card-green: #0f6b38;
    --card-dark: #222326;
    --brand-green: #137a3f;
    --brand-light: #4fb54a;
    --text-white: #ffffff;
    --faint-mark: #1b1c1f;
  }
  * { box-sizing: border-box; margin: 0; padding: 0; }
  html, body {
    width: 1200px; height: 960px; overflow: hidden;
    background: var(--backdrop);
    font-family: "Roboto", sans-serif;
  }
  .card {
    position: absolute; left: 215px; width: 702px; height: 400px; overflow: hidden;
  }
  .card--front { top: 60px; background: var(--card-green); }
  .card--back { top: 500px; background: var(--card-dark); }

  /* front */
  .front-brand {
    position: absolute; left: 0; right: 0; top: 90px;
    display: flex; flex-direction: column; align-items: center;
  }
  .brand-dot {
    width: 140px; height: 140px; border-radius: 50%;
    background: #128043;
  }
  .brand-name {
    margin-top: 22px; font-weight: 500; font-size: 26px; letter-spacing: 3px;
    color: #0c5a2f; text-align: center;
  }
  .brand-phone {
    margin-top: 8px; font-weight: 500; font-size: 13px; letter-spacing: 11px;
    color: #0c5a2f;
  }
  .tagline {
    position: absolute; left: 0; right: 0; top: 357px; text-align: center;
    color: var(--text-white); font-size: 15.5px; letter-spacing: .4px;
  }

  /* back */
  .back-mark {
    position: absolute; left: 10px; top: 40px; width: 370px; height: 330px;
  }
  .back-mark__circle {
    position: absolute; left: 20px; top: 0; width: 330px; height: 330px;
    border-radius: 50%; background: var(--faint-mark);
  }
  .back-mark__name {
    position: absolute; left: 0; right: 0; top: 138px; text-align: center;
    font-weight: 700; font-size: 40px; color: #2a2b2f; letter-spacing: 1px; line-height: 1.1;
  }
  .back-brand {
    position: absolute; left: 470px; width: 210px; top: 28px;
    display: flex; flex-direction: column; align-items: center;
  }
  .back-brand .brand-dot { width: 92px; height: 92px; background: var(--brand-green); }
  .back-brand .brand-name { color: var(--brand-green); font-size: 15px; letter-spacing: 2px; margin-top: 16px; }
  .back-brand .brand-phone { color: var(--brand-green); font-size: 9px; letter-spacing: 8px; margin-top: 6px; }

  .holder-name {
    position: absolute; right: 32px; top: 230px;
    font-size: 35px; color: var(--brand-green); letter-spacing: 1px;
  }
  .holder-name__first { font-weight: 700; }
  .holder-name__last { font-weight: 300; }
  .name-tab {
    position: absolute; right: 0; top: 233px; width: 19px; height: 31px;
    background: var(--brand-green);
  }
  .contact-list {
    position: absolute; right: 27px; top: 312px; list-style: none;
  }
  .contact-list li {
    display: flex; align-items: center; justify-content: flex-end; gap: 8px;
    color: var(--text-white); font-size: 14px; letter-spacing: .5px; height: 21.5px;
  }
  .contact-list svg { width: 14px; height: 14px; fill: var(--brand-green); }
</style>
</head>
<body>
  <section class="card card--front">
    <div class="front-brand">
      <div class="brand-dot"></div>
      <div class="brand-name">TRAVERSE GROUNDMAKRZ</div>
      <div class="brand-phone">555-714-9082</div>
    </div>
    <p class="tagline">SPEACIALIZES IN LAND CLEARING , MUCLHING AND EXCAVATION</p>
  </section>

  <section class="card card--back">
    <div class="back-mark">
      <div class="back-mark__circle"></div>
      <div class="back-mark__name">TRAVERSE<br>GROUNDMAKRZ</div>
    </div>
    <div class="back-brand">
      <div class="brand-dot"></div>
      <div class="brand-name">TRAVERSE GROUNDMAKRZ</div>
      <div class="brand-phone">555-714-9082</div>
    </div>
    <h1 class="holder-name"><span class="holder-name__first">DALE</span> <span class="holder-name__last">VORSKIN</span></h1>
    <div class="name-tab"></div>
    <ul class="contact-list">
      <li>555- 714-9082
        <svg viewBox="0 0 24 24"><path d="M6.6 10.8a15 15 0 0 0 6.6 6.6l2.2-2.2c.3-.3.7-.4 1-.2 1.1.4 2.3.6 3.6.6.6 0 1 .4 1 1V20c0 .6-.4 1-1 1A17 17 0 0 1 3 4c0-.6.4-1 1-1h3.5c.6 0 1 .4 1 1 0 1.3.2 2.5.6 3.6.1.3 0 .7-.2 1z"/></svg>
      </li>
      <li>WWW.TRV-GROUNDMAKRZ.COM
        <svg viewBox="0 0 24 24"><circle cx="12" cy="12" r="10"/></svg>
      </li>
      <li>OFFICE@TRV-GROUNDMAKRZ.COM
        <svg viewBox="0 0 24 24"><path d="M2 6h20v13H2z M2 6l10 7 10-7" stroke="#222326" stroke-width="1.5"/></svg>
      </li>
    </ul>
  </section>
</body>
</html>
```